Business card design Needed for new logo / Construction business, home extensions and new builds

We need a business card design using our new logo files which i will attach to this project :)

We are a small construction business specialising in home extensions, new builds and property development. We are very ambitious and would appreciate professional and elegant designs for our new business card.

Very serious about using the services on MakerQuarry and recently acquired our new logo from here :)

Please get involved, i will feedback when i can as i am very busy but can respond daily, thanks

Target Market(s)

People that want to build onto their houses, new building developments or adding too their existing property

Industry/Entity Type

Construction

Contact Information for Business Card

Renwick Tolliver Construction, Lionel Ashby (Managing Director), Tel 07822254961, email - info@renwick-tolliver, www.renwick-tolliver.co.uk

Colors

Designer to choose colors to be used in the design.

Requirements
Must have
• I like a deep grey on the back please. A lot of you have provided black from and back, try mixing things up a little. The black looks cool 😎 Thanks

```html
<!DOCTYPE html>
<html lang="en">
<head>
<meta charset="utf-8">
<title>Renwick Tolliver Construction – Business Card</title>
<link rel="stylesheet" href="https://fonts.googleapis.com/css2?family=Open+Sans:wght@400;600;700&display=swap">
<style>
  :root {
    --canvas: #2a2d33;
    --card-black: #1d1c21;
    --gold-light: #f6d98a;
    --gold: #e0a93a;
    --gold-deep: #b87a16;
    --silver: #c9ccd1;
    --silver-dark: #8d9196;
    --grey-back-light: #a3a8ae;
    --grey-back: #7d8288;
    --white: #f4f4f4;
  }
  * { box-sizing: border-box; margin: 0; padding: 0; }
  html, body { width: 1200px; height: 780px; overflow: hidden; }
  body {
    background: var(--canvas);
    font-family: "Open Sans", Arial, sans-serif;
    position: relative;
  }
  .card {
    position: absolute;
    top: 230px;
    width: 560px;
    height: 320px;
    border-radius: 3px;
    overflow: hidden;
    box-shadow: 0 10px 28px rgba(0,0,0,0.45);
  }
  .card-front { left: 27px; background: var(--card-black); }
  .card-back  { left: 613px; }

  .front-shapes { position: absolute; inset: 0; }

  .brand {
    position: absolute;
    top: 38px;
    left: 300px;
    display: flex;
    align-items: center;
    gap: 10px;
  }
  .brand-mark {
    width: 14px; height: 14px;
    background: var(--gold);
    flex: none;
  }
  .brand-name {
    font-weight: 600;
    font-size: 15px;
    letter-spacing: 0.5px;
    color: var(--gold);
    line-height: 1.25;
    width: 210px;
  }

  .person { position: absolute; top: 52px; left: 40px; }
  .person-name {
    font-weight: 700;
    font-size: 31px;
    line-height: 1;
    color: var(--silver);
  }
  .person-name .surname { color: var(--gold); }
  .person-title {
    margin-top: 8px;
    margin-left: 30px;
    font-size: 15px;
    color: var(--white);
  }

  .divider {
    position: absolute;
    left: 258px;
    top: 118px;
    width: 2px;
    height: 78px;
    background: var(--white);
  }

  .contacts {
    position: absolute;
    left: 276px;
    top: 120px;
    list-style: none;
  }
  .contacts li {
    display: flex;
    align-items: center;
    gap: 9px;
    font-size: 16px;
    color: var(--white);
    height: 25px;
  }
  .contacts svg { width: 14px; height: 14px; flex: none; }

  .address {
    position: absolute;
    left: 40px;
    top: 272px;
    font-size: 15px;
    color: var(--white);
    text-shadow: 0 1px 1px rgba(120,70,0,0.35);
  }

  .back-surface {
    position: absolute;
    inset: 0;
    background: linear-gradient(120deg, var(--grey-back) 0%, var(--grey-back-light) 55%, var(--grey-back) 100%);
  }
  .back-brand {
    position: absolute;
    right: 22px;
    bottom: 18px;
    display: flex;
    align-items: center;
    gap: 6px;
  }
  .back-brand .brand-mark { width: 8px; height: 8px; background: var(--white); }
  .back-brand .brand-name {
    font-size: 8px;
    width: auto;
    color: var(--white);
  }
</style>
</head>
<body>

<section class="card card-front" aria-label="Business card front">
  <svg class="front-shapes" viewBox="0 0 560 320" aria-hidden="true">
    <defs>
      <linearGradient id="goldBand" x1="0" y1="0" x2="0.3" y2="1">
        <stop offset="0" stop-color="#f6d98a"/>
        <stop offset="0.45" stop-color="#e0a93a"/>
        <stop offset="1" stop-color="#b87a16"/>
      </linearGradient>
      <linearGradient id="silverLine" x1="0" y1="0" x2="1" y2="0">
        <stop offset="0" stop-color="#8d9196"/>
        <stop offset="0.5" stop-color="#e6e8eb"/>
        <stop offset="1" stop-color="#8d9196"/>
      </linearGradient>
    </defs>
    <path d="M0,160 C120,235 300,258 560,268 L560,320 L0,320 Z" fill="url(#goldBand)"/>
    <path d="M60,125 C150,220 330,250 560,258" fill="none" stroke="url(#silverLine)" stroke-width="4" stroke-linecap="round"/>
  </svg>

  <div class="brand">
    <span class="brand-mark"></span>
    <span class="brand-name">Renwick Tolliver Construction</span>
  </div>

  <div class="person">
    <p class="person-name">Lionel <span class="surname">Ashby</span></p>
    <p class="person-title">Managing Director</p>
  </div>

  <span class="divider"></span>

  <ul class="contacts">
    <li>
      <svg viewBox="0 0 16 16" aria-hidden="true"><path d="M4 1.5l2.2 3-1.4 1.6c.8 1.8 2.3 3.3 4.1 4.1l1.6-1.4 3 2.2-1.2 2.5C7.5 13.3 2.7 8.5 1.5 3z" fill="#e0a93a"/></svg>
      <span>0782 225 4961</span>
    </li>
    <li>
      <svg viewBox="0 0 16 16" aria-hidden="true"><circle cx="8" cy="8" r="6.5" fill="none" stroke="#e0a93a" stroke-width="1.6"/><path d="M1.5 8h13M8 1.5c-3 3.5-3 9.5 0 13M8 1.5c3 3.5 3 9.5 0 13" fill="none" stroke="#e0a93a" stroke-width="1.2"/></svg>
      <span>info@renwick-tolliver.co.uk</span>
    </li>
    <li>
      <svg viewBox="0 0 16 16" aria-hidden="true"><rect x="1.5" y="3.5" width="13" height="9" fill="none" stroke="#e0a93a" stroke-width="1.6"/><path d="M1.5 3.5l6.5 5.5 6.5-5.5" fill="none" stroke="#e0a93a" stroke-width="1.4"/></svg>
      <span>www.renwick-tolliver.co.uk</span>
    </li>
  </ul>

  <p class="address">Hollin Lane, Westbury Kingsmead, KM4 7RT</p>
</section>

<section class="card card-back" aria-label="Business card back">
  <div class="back-surface" role="img" aria-label="Deep grey surface with a repeating monogram pattern"></div>
  <div class="back-brand">
    <span class="brand-mark"></span>
    <span class="brand-name">Renwick Tolliver Construction</span>
  </div>
</section>

</body>
</html>
```